Corporate Business Card

Very professional, Modern, Not to busy, include phone address email, website
(253) 617-4930, 18761 52nd Avenue S, Ashbury, OR 98047, martin@plumlinegroup.com, varkoworks.com

Target Market(s)

Manufacturing

Industry/Entity Type

Aero, machining, manufacturing, Off road racing

Contact Information for Business Card

Phone, address email, website

```html
<!DOCTYPE html>
<html lang="en">
<head>
<meta charset="utf-8">
<title>Varko Works – Business Card</title>
<link rel="stylesheet" href="https://fonts.googleapis.com/css2?family=Open+Sans:wght@400;700&display=swap">
<style>
  :root {
    --navy: #1b3a7c;
    --navy-deep: #17336f;
    --navy-soft: #234a8a;
    --red: #d2232a;
    --card-white: #f5f5f5;
    --ink: #1f1f24;
    --backdrop: #e6e6e6;
  }
  * { box-sizing: border-box; margin: 0; padding: 0; }
  html, body {
    width: 1084px;
    height: 1200px;
    overflow: hidden;
  }
  body {
    background: var(--backdrop);
    font-family: "Open Sans", Arial, sans-serif;
    position: relative;
  }
  .card {
    position: absolute;
    left: 162px;
    width: 760px;
    height: 434px;
    box-shadow: 0 6px 14px rgba(0, 0, 0, 0.22);
    overflow: hidden;
  }

  /* Back side */
  .card-back {
    top: 110px;
    background: var(--navy);
  }
  .card-back .pattern-field {
    position: absolute;
    inset: 0;
    background: linear-gradient(135deg, var(--navy-soft) 0%, var(--navy) 45%, var(--navy-deep) 100%);
  }
  .card-back .wordmark {
    position: absolute;
    left: 460px;
    top: 310px;
    display: flex;
    align-items: center;
    gap: 10px;
    color: #ffffff;
    font-weight: 700;
    font-size: 30px;
    letter-spacing: 1px;
  }
  .card-back .wordmark-square {
    width: 14px;
    height: 14px;
    background: var(--red);
  }

  /* Front side */
  .card-front {
    top: 656px;
    background: var(--card-white);
  }
  .contact-block {
    position: absolute;
    left: 63px;
    top: 56px;
    color: var(--ink);
  }
  .person-name {
    color: var(--navy);
    font-weight: 700;
    font-size: 29px;
    line-height: 1.1;
  }
  .person-title {
    font-size: 21px;
    line-height: 1.2;
    margin-top: 2px;
  }
  .address {
    margin-top: 50px;
    font-size: 19px;
    line-height: 1.45;
  }
  .contact-list {
    list-style: none;
    margin-top: 24px;
    font-size: 19px;
    line-height: 1.55;
  }
  .contact-list li {
    display: flex;
    align-items: center;
    gap: 8px;
  }
  .contact-list svg {
    width: 15px;
    height: 15px;
    flex: none;
  }
  .card-front .wordmark {
    position: absolute;
    right: 62px;
    top: 204px;
    display: flex;
    align-items: center;
    gap: 12px;
    color: var(--navy);
    font-weight: 700;
    font-size: 38px;
    letter-spacing: 1px;
  }
  .card-front .wordmark-square {
    width: 16px;
    height: 16px;
    background: var(--red);
  }
  .base-bands {
    position: absolute;
    left: 0;
    bottom: 0;
    width: 760px;
    height: 18px;
  }
</style>
</head>
<body>

  <section class="card card-back" aria-label="Business card, back side">
    <div class="pattern-field" role="img" aria-label="Faint repeating brand pattern in tones of navy blue"></div>
    <div class="wordmark">
      <span class="wordmark-square"></span>
      <span class="wordmark-name">Varko Works</span>
    </div>
  </section>

  <section class="card card-front" aria-label="Business card, front side">
    <div class="contact-block">
      <h1 class="person-name">DANIEL REEVES</h1>
      <p class="person-title">Account Manager</p>
      <p class="address">18761 52nd Avenue S<br>Ashbury, OR 98047</p>
      <ul class="contact-list">
        <li>
          <svg viewBox="0 0 16 16" aria-hidden="true"><path fill="#d2232a" d="M3.6 1.5l2.3 2.6-1.3 1.6c.9 2 2.6 3.7 4.6 4.6l1.6-1.3 2.6 2.3-1.3 2.1C7 12.9 3.1 9 2 3l1.6-1.5z"/></svg>
          <span>(253) 617-4930</span>
        </li>
        <li>
          <svg viewBox="0 0 16 16" aria-hidden="true"><rect x="1.5" y="3.5" width="13" height="9" fill="#d2232a"/><path d="M1.5 3.5L8 9l6.5-5.5" fill="none" stroke="#f5f5f5" stroke-width="1.2"/></svg>
          <span>martin@plumlinegroup.com</span>
        </li>
        <li>
          <svg viewBox="0 0 16 16" aria-hidden="true"><g fill="none" stroke="#d2232a" stroke-width="1.3"><circle cx="8" cy="8" r="6.3"/><ellipse cx="8" cy="8" rx="2.8" ry="6.3"/><path d="M1.7 8h12.6M2.8 4.8h10.4M2.8 11.2h10.4"/></g></svg>
          <span>varkoworks.com</span>
        </li>
      </ul>
    </div>

    <div class="wordmark">
      <span class="wordmark-square"></span>
      <span class="wordmark-name">Varko Works</span>
    </div>

    <svg class="base-bands" viewBox="0 0 760 18" preserveAspectRatio="none" aria-hidden="true">
      <polygon points="0,0 440,0 434,18 0,18" fill="var(--navy)"/>
      <polygon points="446,0 760,0 760,18 440,18" fill="var(--red)"/>
    </svg>
  </section>

</body>
</html>
```